Stationery Design Task - Stationary, memo and report templates for professional services company

Looking for someone to update stationary design but just as importantly come up with a template for reports and memos for use in our consulting firm. Would also like some brand use guidelines to be able to share with our whole team. We have an existing logo that we like. Need to update with a more contemporary look so that our deliverables to clients look good and professional yet stylish. This is for business to business communications. No need for envelope design. Important to have design for multiple pages, i.e. first page of a report and then 2nd page. Need to use in MS word documents so must be easy to use and replicate. Don't want something overly complex. Clean, fresh looking is best.

Industry/Entity Type

Information Technology

Font styles to use
Sans Serif

Colors
33a6d7
0792cd
85cae6
cee9f5
cedeed
85abd2
3377b5
0455a3

Requirements
Must have
• Clean look but with a little style or pop. Something that can easily be used in word documents. Need to have page styles that have a first page of a report (not a cover page) and then secondary page.
Nice to have
• - Although the dark blue is our primary color. Might be willing to look at some accent color as well.
Should not have
• Not just our logo on the page with a color bar.

```html
<!DOCTYPE html>
<html lang="en">
<head>
<meta charset="utf-8">
<title>Northwave Systems – Report Template Set</title>
<link href="https://fonts.googleapis.com/css2?family=Roboto:wght@400;500;700;900&display=swap" rel="stylesheet">
<style>
:root{
  --backdrop:#5b5b5d;
  --blue:#0792cd;
  --blue-deep:#0a78c8;
  --blue-mid:#33a6d7;
  --blue-soft:#85cae6;
  --blue-pale:#cee9f5;
  --ink:#555a60;
  --ink-soft:#8a8f95;
  --bar-grey:#6f6f6f;
  --label-grey:#5c5f63;
  --page-top:#ffffff;
  --page-bottom:#dcdde0;
}
*{box-sizing:border-box;margin:0;padding:0}
html,body{width:1200px;height:651px;overflow:hidden;background:var(--backdrop);font-family:"Roboto",Arial,sans-serif}
.canvas{position:relative;width:1200px;height:651px;background:var(--backdrop)}
.page{position:absolute;width:208px;height:291px;background:linear-gradient(180deg,var(--page-top) 0%,var(--page-top) 35%,var(--page-bottom) 100%);overflow:hidden;color:var(--ink)}
.row-1{top:28px}.row-2{top:337px}
.col-1{left:38px}.col-2{left:266px}.col-3{left:496px}.col-4{left:725px}.col-5{left:954px}
.corner-art{position:absolute;top:0;right:0;width:48px;height:50px;background:linear-gradient(225deg,var(--blue-deep) 0%,var(--blue) 45%,var(--blue-soft) 100%)}
.page-title{position:absolute;left:16px;top:22px;font-size:8.4px;color:var(--blue);font-weight:400}
.title-rule{position:absolute;left:16px;top:34px;width:155px;height:0;border-top:0.6px solid #b8bcc2}
.footer{position:absolute;left:0;bottom:0;width:100%;height:16px;background:var(--blue);color:#fff;font-size:3.9px;text-align:right;padding:3px 12px 0 0;line-height:5px}
.body-text{font-size:3.9px;line-height:6.2px;color:var(--ink-soft);text-align:justify}
/* cover */
.cover-art{position:absolute;left:66px;top:0;width:142px;height:150px;background:linear-gradient(200deg,var(--blue-deep) 0%,var(--blue) 55%,var(--blue-mid) 100%)}
.cover-name{position:absolute;left:90px;top:54px;color:#fff;font-size:15px;font-weight:700;line-height:15px}
.brand{position:absolute;left:24px;top:176px;display:flex;align-items:center;gap:6px}
.brand-dot{width:26px;height:26px;border-radius:50%;background:var(--blue)}
.brand-name{font-size:21px;font-weight:700;color:var(--blue);letter-spacing:0.2px;line-height:1}
.cover-title{position:absolute;left:0;width:100%;text-align:center;top:229px;font-size:9.4px;font-weight:700;color:#3f4348;letter-spacing:.3px}
.cover-date{position:absolute;left:0;width:100%;text-align:center;top:248px;font-size:7px;font-weight:700;color:var(--blue)}
/* toc */
.toc{position:absolute;left:17px;top:43px;width:177px;list-style:none}
.toc li{display:flex;align-items:flex-end;font-size:4.4px;height:8.24px;color:var(--ink-soft)}
.toc li.major{color:var(--blue);font-weight:500}
.toc .leader{flex:1;border-bottom:0.5px dotted #b0b4ba;margin:0 2px 1.3px}
.toc .num{color:var(--ink-soft);font-weight:400}
/* about */
.photo{position:absolute;left:19px;top:46px;width:98px;height:97px;background:linear-gradient(135deg,#e7e2dc 0%,#c9b8a5 45%,#8d8a86 100%)}
.about-side{position:absolute;left:119px;top:44px;width:70px}
.about-main{position:absolute;left:19px;top:145px;width:170px}
/* team */
.member{position:absolute;width:70px;text-align:center}
.hex-photo{display:block;margin:0 auto 2px;width:50px;height:43px}
.member-name{font-size:5px;font-weight:700;color:var(--blue);line-height:6px}
.member-role{font-size:4.2px;color:#4a4e53;line-height:5px;margin-bottom:3px}
.member .body-text{text-align:center;line-height:5.6px}
/* bars */
.intro{position:absolute;left:18px;top:48px;width:172px}
.outro{position:absolute;left:18px;top:236px;width:172px}
.chart{position:absolute;left:0;top:106px;width:208px;height:126px}
/* letterhead */
.lh-brand{position:absolute;left:20px;top:22px;display:flex;align-items:center;gap:5px}
.lh-brand .brand-dot{width:16px;height:16px}
.lh-brand .brand-name{font-size:13px}
.letter{position:absolute;left:20px;top:98px;width:170px}
.salute{font-size:5px;color:#4a4e53;margin-bottom:7px}
.letter p{font-size:3.3px;line-height:4.6px;color:var(--ink-soft);margin-bottom:5px;text-align:left}
.signature{width:42px;height:16px;margin-top:3px;background:linear-gradient(90deg,#cfe6f4,#9ec8e6)}
.lh-footer{text-align:center;padding:2px 0 0;font-size:3.6px;line-height:5px}
/* graphic chart */
.ring{position:absolute;width:52px;text-align:center}
.ring svg{display:block;width:52px;height:52px}
.ring-label{display:inline-block;margin-top:3px;background:var(--label-grey);color:#fff;font-size:3.6px;width:40px;height:6px;line-height:6px}
/* pie */
.pie{position:absolute;left:16px;top:50px;width:60px;height:60px}
.legend{position:absolute;left:87px;top:54px;list-style:none}
.legend li{display:flex;align-items:center;gap:3px;font-size:3.9px;color:#4a4e53;height:9px}
.swatch{width:5px;height:5px}
.pie-note{position:absolute;left:86px;top:76px;width:104px;text-align:left}
.pie-main{position:absolute;left:18px;top:121px;width:172px}
/* thank you */
.thanks{background:none}
.thanks-art{position:absolute;inset:0;background:linear-gradient(160deg,var(--blue-deep) 0%,var(--blue) 55%,var(--blue-mid) 100%)}
.thanks-text{position:absolute;left:0;top:102px;width:160px;text-align:center;color:#fff;font-size:17px;font-weight:700;line-height:19px}
.contact{position:absolute;left:124px;top:228px;width:80px;text-align:center;color:#fff;font-size:3.6px;line-height:4.8px}
.contact h3{font-size:4.2px;font-weight:700;margin-bottom:2px}
</style>
</head>
<body>
<main class="canvas">

  <!-- Cover -->
  <section class="page cover row-1 col-1">
    <div class="cover-art" role="img" aria-label="Blue hexagon pattern decoration"></div>
    <div class="cover-name">CLEAR<br>PEAK</div>
    <div class="brand"><span class="brand-dot"></span><span class="brand-name">NORTHWAVE</span></div>
    <div class="cover-title">IT SUPPORT GUIDE</div>
    <div class="cover-date">SEPTEMBER 2018</div>
    <div class="footer">copyright2008@northwavesystems.com, All Rights Reserved</div>
  </section>

  <!-- Table of contents -->
  <section class="page row-1 col-2">
    <div class="corner-art" role="img" aria-label="Blue hexagon corner decoration"></div>
    <h2 class="page-title">Table of content</h2>
    <div class="title-rule"></div>
    <ul class="toc">
      <li class="major">What's New<span class="leader"></span><span class="num">2</span></li>
      <li>Proin pede metus, vulputate nec, fermentum fringil<span class="leader"></span><span class="num">2</span></li>
      <li class="major">Vehicula<span class="leader"></span><span class="num">5</span></li>
      <li>Vitae, justo d<span class="leader"></span><span class="num">5</span></li>
      <li>Etiam neque. Fusce<span class="leader"></span><span class="num">5</span></li>
      <li class="major">Tellus odio, d<span class="leader"></span><span class="num">8</span></li>
      <li>apibus id ferment<span class="leader"></span><span class="num">8</span></li>
      <li class="major">Um quis, suscipit id ers<span class="leader"></span><span class="num">10</span></li>
      <li>Duis pulvinar. Etiam<span class="leader"></span><span class="num">10</span></li>
      <li>egestas wisi a erat. Vi<span class="leader"></span><span class="num">10</span></li>
      <li class="major">Vamus luctus egestas<span class="leader"></span><span class="num">15</span></li>
      <li>leo. Aenean vel massa<span class="leader"></span><span class="num">15</span></li>
      <li class="major">Quis massa vehicula<span class="leader"></span><span class="num">17</span></li>
      <li>lacinia. Nullam at arcu<span class="leader"></span><span class="num">18</span></li>
      <li class="major">a est sollicitudin euism<span class="leader"></span><span class="num">18</span></li>
      <li>od. Et harum quidem r<span class="leader"></span><span class="num">22</span></li>
      <li>erum facilis est et exp<span class="leader"></span><span class="num">22</span></li>
      <li>edita distinctio. Nulla<span class="leader"></span><span class="num">22</span></li>
      <li class="major">turpis magna, cursus s<span class="leader"></span><span class="num">23</span></li>
      <li>it amet, suscipit a, int<span class="leader"></span><span class="num">23</span></li>
      <li>erdum id, felis. Sed ac<span class="leader"></span><span class="num">25</span></li>
      <li>dolor sit amet purus m<span class="leader"></span><span class="num">25</span></li>
      <li class="major">alesuada congue.Cur<span class="leader"></span><span class="num">27</span></li>
      <li>abitur sagittis hendreri<span class="leader"></span><span class="num">27</span></li>
      <li>t ante. In rutrum. Nulla<span class="leader"></span><span class="num">27</span></li>
    </ul>
    <div class="footer">copyright2008@northwavesystems.com, All Rights Reserved<br>Page2</div>
  </section>

  <!-- About us -->
  <section class="page row-1 col-3">
    <div class="corner-art" role="img" aria-label="Blue hexagon corner decoration"></div>
    <h2 class="page-title">About Us</h2>
    <div class="title-rule"></div>
    <div class="photo" role="img" aria-label="Photo of three colleagues together in a bright office"></div>
    <p class="body-text about-side">Lorem ipsum dolor sit amet, consectetur adipiscing elit. Donec orci purus, luctus vitae dignissim eu, iaculis sed purus. Vivamus faucibus, ipsum nec aliquet viverra, leo mauris condimentum ligula, sit amet sagittis enim ligula quis arcu. Nam egestas tortor id nisi porttitor mattis. In tortor ante, ultricies in suscipit a, tempus non massa. Vivamus et auctor mi. Fusce vel massa nulla. Phasellus nec eros mauris, et scelerisque orci. Donec malesuada orci.</p>
    <p class="body-text about-main">Lorem ipsum dolor sit amet, consectetur adipiscing elit. Donec orci purus, luctus vitae dignissim eu, iaculis sed purus. Vivamus faucibus, ipsum nec aliquet viverra, leo mauris condimentum ligula, sit amet sagittis enim ligula quis arcu. Nam egestas tortor id nisi porttitor mattis. In tortor ante, ultricies in suscipit a, tempus non massa. Vivamus et auctor mi. Fusce vel massa nulla. Phasellus nec eros mauris, et scelerisque orci. Donec malesuada orci vitae nulla accumsan porta a id massa. Quisque accumsan iaculis magna sit amet fringilla. Maecenas consequat, magna eget tincidunt semper, odio nibh rutrum mi, id feugiat ante nisi eu risus. Vestibulum nunc orci, rhoncus a placerat in, ultricies in mi. Cras mattis varius eros, vel.</p>
    <div class="footer">copyright2008@northwavesystems.com, All Rights Reserved<br>Page3</div>
  </section>

  <!-- Our team -->
  <section class="page row-1 col-4">
    <div class="corner-art" role="img" aria-label="Blue hexagon corner decoration"></div>
    <h2 class="page-title">Our team</h2>
    <div class="title-rule"></div>
    <div class="member" style="left:21px;top:52px">
      <svg class="hex-photo" viewBox="0 0 50 43" role="img" aria-label="Portrait of the managing director"><polygon points="50,21.5 37.5,43 12.5,43 0,21.5 12.5,0 37.5,0" fill="#9a8d82"/></svg>
      <div class="member-name">DANIEL REYES</div><div class="member-role">Managing Director</div>
      <p class="body-text">Lorem ipsum dolor sit amet, consectetur adipis icing elit, sed do eiusmod tempor incididunt ut</p>
    </div>
    <div class="member" style="left:106px;top:52px">
      <svg class="hex-photo" viewBox="0 0 50 43" role="img" aria-label="Portrait of the accountant"><polygon points="50,21.5 37.5,43 12.5,43 0,21.5 12.5,0 37.5,0" fill="#b9a48f"/></svg>
      <div class="member-name">NADIA</div><div class="member-role">Accountant</div>
      <p class="body-text">Lorem ipsum dolor sit amet, consectetur adipis icing elit, sed do eiusmod tempor incididunt ut</p>
    </div>
    <div class="member" style="left:21px;top:163px">
      <svg class="hex-photo" viewBox="0 0 50 43" role="img" aria-label="Portrait of the marketing manager"><polygon points="50,21.5 37.5,43 12.5,43 0,21.5 12.5,0 37.5,0" fill="#a39080"/></svg>
      <div class="member-name">OWEN HALE</div><div class="member-role">Marketing manager</div>
      <p class="body-text">Lorem ipsum dolor sit amet, consectetur adipis icing elit, sed do eiusmod tempor incididunt ut</p>
    </div>
    <div class="member" style="left:106px;top:163px">
      <svg class="hex-photo" viewBox="0 0 50 43" role="img" aria-label="Portrait of the accountant"><polygon points="50,21.5 37.5,43 12.5,43 0,21.5 12.5,0 37.5,0" fill="#7e6a5c"/></svg>
      <div class="member-name">LENA</div><div class="member-role">Accountant</div>
      <p class="body-text">Lorem ipsum dolor sit amet, consectetur adipis icing elit, sed do eiusmod tempor incididunt ut</p>
    </div>
    <div class="footer">copyright2008@northwavesystems.com, All Rights Reserved<br>Page4</div>
  </section>

  <!-- Bar charts -->
  <section class="page row-1 col-5">
    <div class="corner-art" role="img" aria-label="Blue hexagon corner decoration"></div>
    <h2 class="page-title">Bar charts</h2>
    <div class="title-rule"></div>
    <p class="body-text intro">Lorem ipsum dolor sit amet, consectetur adipisicing elit, sed do eiusmod tempor incididunt ut labore et dolore magna aliqua. Ut enim ad minim veniam, quis nostrud exercitation ullamco laboris nisi ut aliquip ex ea commodo consequat. Duis aute irure dolor in reprehenderit in voluptate velit esse cillum dolore eu fugiat nulla pariatur. Excepteur sint occaecat cupidatat non proident, sunt in culpa qui officia deserunt mollit anim id est laborum.</p>
    <svg class="chart" viewBox="0 0 208 126" font-family="Roboto,Arial,sans-serif">
      <g stroke="#d5d8dc" stroke-width="0.4">
        <line x1="25" y1="10" x2="200" y2="10"/><line x1="25" y1="20" x2="200" y2="20"/>
        <line x1="25" y1="30" x2="200" y2="30"/><line x1="25" y1="40" x2="200" y2="40"/>
        <line x1="25" y1="50" x2="200" y2="50"/><line x1="25" y1="60" x2="200" y2="60"/>
        <line x1="25" y1="70" x2="200" y2="70"/><line x1="25" y1="80" x2="200" y2="80"/>
        <line x1="25" y1="90" x2="200" y2="90"/><line x1="25" y1="100" x2="200" y2="100"/>
      </g>
      <line x1="25" y1="110" x2="200" y2="110" stroke="#8a8f95" stroke-width="0.5"/>
      <g font-size="4.2" fill="#6a6f75" text-anchor="end">
        <text x="21" y="11.5">5</text><text x="21" y="21.5">4.5</text><text x="21" y="31.5">4</text>
        <text x="21" y="41.5">3.5</text><text x="21" y="51.5">3</text><text x="21" y="61.5">2.5</text>
        <text x="21" y="71.5">2</text><text x="21" y="81.5">1.5</text><text x="21" y="91.5">1</text>
        <text x="21" y="101.5">0.5</text><text x="21" y="111.5">0</text>
      </g>
      <rect x="40" y="26" width="14" height="84" fill="#0792cd"/>
      <rect x="57" y="38" width="14" height="72" fill="#6f6f6f"/>
      <rect x="74" y="58" width="14" height="52" fill="#0792cd"/>
      <rect x="127" y="48" width="14" height="62" fill="#0792cd"/>
      <rect x="144" y="20" width="14" height="90" fill="#6f6f6f"/>
      <rect x="161" y="58" width="14" height="52" fill="#0792cd"/>
      <g font-size="3.8" fill="#fff">
        <text transform="translate(49,108) rotate(-90)">Sub text1</text>
        <text transform="translate(66,108) rotate(-90)">Sub text2</text>
        <text transform="translate(83,108) rotate(-90)">Sub text3</text>
        <text transform="translate(136,108) rotate(-90)">Sub text1</text>
        <text transform="translate(153,108) rotate(-90)">Sub text2</text>
        <text transform="translate(170,108) rotate(-90)">Sub text3</text>
      </g>
      <g font-size="4" fill="#4a4e53" text-anchor="middle">
        <text x="64" y="118">Gategory 1</text><text x="151" y="118">Gategory 2</text>
      </g>
    </svg>
    <p class="body-text outro">Duis aute irure dolor in reprehenderit in voluptate velit esse cillum dolore eu fugiat nulla pariatur. Excepteur sint occaecat cupidatat non proident, sunt in culpa qui officia deserunt mollit anim id est laborum.</p>
    <div class="footer">copyright2008@northwavesystems.com, All Rights Reserved<br>Page5</div>
  </section>

  <!-- Letterhead -->
  <section class="page row-2 col-1">
    <div class="corner-art" role="img" aria-label="Blue hexagon corner decoration"></div>
    <div class="lh-brand"><span class="brand-dot"></span><span class="brand-name">NORTHWAVE</span></div>
    <div class="letter">
      <div class="salute">Dear Mr. Reyes,</div>
      <p>Lorem ipsum dolor sit amet, consectetur adipiscing elit. Donec orci purus, luctus vitae dignissim eu, iaculis sed purus. Vivamus faucibus, ipsum nec aliquet viverra, leo mauris condimentum ligula, sit amet sagittis enim ligula quis arcu. Nam egestas tortor id nisi porttitor mattis. In tortor ante, ultricies in suscipit a, tempus non massa. Vivamus et auctor mi. Fusce vel massa nulla.</p>
      <p>Donec malesuada orci vitae nulla accumsan porta a id massa. Quisque accumsan iaculis magna sit amet fringilla. Maecenas consequat, magna eget tincidunt semper, odio nibh rutrum mi, id feugiat ante nisi eu risus. Vestibulum nunc orci, rhoncus a placerat in, ultricies in mi. Cras mattis varius eros, vel fringilla nisi suscipit eget.</p>
      <p>Sed id augue vitae urna euismod commodo aliquet a quam. Pellentesque arcu velit, cursus et malesuada ut, consequat et diam. Nullam erat sem, rhoncus id ullamcorper vitae, rhoncus et arcu. In ultricies ultricies nulla, ut rutrum nisi iaculis at. Donec ac magna a metus ornare faucibus. Fusce aliquet faucibus ultricies.</p>
      <p>It is a long established fact that a reader will be distracted by the readable content of a page when looking at its layout. The point of using it is that it has a more even distribution of letters, making it look like readable text.</p>
      <p style="margin-top:8px">Sincerely,</p>
      <div class="signature" role="img" aria-label="Handwritten signature"></div>
    </div>
    <div class="footer lh-footer">214 HARBOR VIEW ROAD, BROOKFIELD, OREGON 97410 &nbsp;|&nbsp; 555 014 2290 &nbsp;|&nbsp; INFO@NORTHWAVESYSTEMS.COM<br>www.northwavesystems.com</div>
  </section>

  <!-- Blank continuation page -->
  <section class="page row-2 col-2"></section>

  <!-- Graphic chart -->
  <section class="page row-2 col-3">
    <div class="corner-art" role="img" aria-label="Blue hexagon corner decoration"></div>
    <h2 class="page-title">Graphic chart</h2>
    <div class="title-rule"></div>
    <p class="body-text intro">incididunt ut labore et dolore magna aliqua. Ut enim ad minim veniam, quis nostrud exercitation ullamco laboris nisi ut aliquip ex ea commodo consequat. Duis aute irure dolor in reprehenderit in voluptate velit esse cillum dolore eu fugiat nulla pariatur. Excepteur sint occaecat cupidatat non proident, sunt in culpa qui officia deserunt mollit anim id est laborum.</p>
    <div class="ring" style="left:36px;top:107px">
      <svg viewBox="0 0 54 54"><circle cx="27" cy="27" r="23" fill="none" stroke="#a9adb2" stroke-width="3.5"/><circle cx="27" cy="27" r="23" fill="none" stroke="#0792cd" stroke-width="3.5" stroke-dasharray="130 144.5" transform="rotate(-90 27 27)"/><text x="27" y="31" text-anchor="middle" font-family="Roboto,Arial,sans-serif" font-weight="700" font-size="11" fill="#0792cd">90%</text></svg>
      <span class="ring-label">dolor sit</span>
    </div>
    <div class="ring" style="left:112px;top:107px">
      <svg viewBox="0 0 54 54"><circle cx="27" cy="27" r="23" fill="none" stroke="#a9adb2" stroke-width="3.5"/><circle cx="27" cy="27" r="23" fill="none" stroke="#0792cd" stroke-width="3.5" stroke-dasharray="46 144.5" transform="rotate(-90 27 27)"/><text x="27" y="31" text-anchor="middle" font-family="Roboto,Arial,sans-serif" font-weight="700" font-size="11" fill="#0792cd">32%</text></svg>
      <span class="ring-label">dolor sit</span>
    </div>
    <div class="ring" style="left:36px;top:186px">
      <svg viewBox="0 0 54 54"><circle cx="27" cy="27" r="23" fill="none" stroke="#a9adb2" stroke-width="3.5"/><circle cx="27" cy="27" r="23" fill="none" stroke="#0792cd" stroke-width="3.5" stroke-dasharray="97 144.5" transform="rotate(-90 27 27)"/><text x="27" y="31" text-anchor="middle" font-family="Roboto,Arial,sans-serif" font-weight="700" font-size="11" fill="#0792cd">67%</text></svg>
      <span class="ring-label">dolor sit</span>
    </div>
    <div class="ring" style="left:112px;top:186px">
      <svg viewBox="0 0 54 54"><circle cx="27" cy="27" r="23" fill="none" stroke="#a9adb2" stroke-width="3.5"/><circle cx="27" cy="27" r="23" fill="none" stroke="#0792cd" stroke-width="3.5" stroke-dasharray="108 144.5" transform="rotate(-90 27 27)"/><text x="27" y="31" text-anchor="middle" font-family="Roboto,Arial,sans-serif" font-weight="700" font-size="11" fill="#0792cd">75%</text></svg>
      <span class="ring-label">dolor sit</span>
    </div>
    <div class="footer">copyright2008@northwavesystems.com, All Rights Reserved<br>Page6</div>
  </section>

  <!-- Pie charts -->
  <section class="page row-2 col-4">
    <div class="corner-art" role="img" aria-label="Blue hexagon corner decoration"></div>
    <h2 class="page-title">Pie charts</h2>
    <div class="title-rule"></div>
    <svg class="pie" viewBox="0 0 60 60">
      <circle cx="30" cy="30" r="21" fill="none" stroke="#0792cd" stroke-width="13" stroke-dasharray="15.5 1" transform="rotate(-90 30 30)"/>
      <circle cx="30" cy="30" r="21" fill="none" stroke="#6f6f6f" stroke-width="13" stroke-dasharray="15.5 17.5" stroke-dashoffset="-16.5" transform="rotate(-90 30 30)"/>
      <circle cx="30" cy="30" r="9" fill="#fff"/>
      <circle cx="30" cy="30" r="6.5" fill="#0792cd"/>
      <circle cx="30" cy="30" r="3" fill="#fff"/>
    </svg>
    <ul class="legend">
      <li><span class="swatch" style="background:#0792cd"></span>Lorem ipsum dolor sit amet 50%</li>
      <li><span class="swatch" style="background:#6f6f6f"></span>Duis aute irure dolor in 50%</li>
    </ul>
    <p class="body-text pie-note">incididunt ut labore et dolore magna aliqua. Ut enim ad minim veniam, quis nostrud exercitation ullamco laboris nisi ut aliquip ex ea commodo consequat.</p>
    <p class="body-text pie-main">Lorem ipsum dolor sit amet, consectetur adipiscing elit. Donec orci purus, luctus vitae dignissim eu, iaculis sed purus. Vivamus faucibus, ipsum nec aliquet viverra, leo mauris condimentum ligula, sit amet sagittis enim ligula quis arcu. Nam egestas tortor id nisi porttitor mattis. In tortor ante, ultricies in suscipit a, tempus non massa. Vivamus et auctor mi. Fusce vel massa nulla. Phasellus nec eros mauris, et scelerisque orci. Donec malesuada orci vitae nulla accumsan porta a id massa. Quisque accumsan iaculis magna sit amet fringilla. Maecenas consequat, magna eget tincidunt semper, odio nibh rutrum mi, id feugiat ante nisi eu risus. Vestibulum nunc orci, rhoncus a placerat in, ultricies in mi. Cras mattis varius eros, vel fringilla nisi suscipit eget. Quisque scelerisque sagittis nulla at porttitor. Sed id augue vitae urna euismod commodo aliquet a quam. Pellentesque arcu velit, cursus et malesuada ut, consequat et diam. Nullam erat sem, rhoncus id ullamcorper vitae, rhoncus et arcu. In ultricies ultricies nulla, ut rutrum nisi iaculis at. Donec ac magna a metus ornare faucibus. Fusce aliquet faucibus ultricies. Morbi semper, est id tincidunt gravida, sem arcu adipiscing lacus, ac bibendum nulla leo eu purus. Quisque nec diam sed.</p>
    <div class="footer">copyright2008@northwavesystems.com, All Rights Reserved<br>Page7</div>
  </section>

  <!-- Back page -->
  <section class="page thanks row-2 col-5">
    <div class="thanks-art" role="img" aria-label="Full-page blue hexagon pattern background"></div>
    <div class="thanks-text">THANK<br>YOU</div>
    <div class="contact">
      <h3>CONTACT US</h3>
      214 HARBOR VIEW ROAD<br>BROOKFIELD, OREGON 97410<br>555 014 2290<br>INFO@NORTHWAVESYSTEMS.COM<br>NORTHWAVESYSTEMS.COM
    </div>
  </section>

</main>
</body>
</html>
```